Valdane Companies Business Card Design

We need a new business card for our Private Equity Real Estate Development firm, “Valdane” and our EB-5 regional center “Thornmere Regional Center” on one card. We prefer a design that is simple, elegant, and represents the luxury products we design and build as well as the financial security and stability our successful history has produced. We are an industry leader in our field and 3rd generation family business that has evolved into an institutional quality investment platform. Considered design size is standard business card dimensions (3.5 x 2 inches with an additional 1/8 inch space for design elements or backgrounds that extend beyond the finished size of your piece.

Target Market(s)

• High net worth individuals
• Highly skilled technical workers and physicians in the US seeking investment-based immigration opportunities
• Sophisticated private equity investors
• Intermediary partners include domestic attorneys and investment brokers, as well as international agent networks
• US real estate developers

Industry/Entity Type

Finance

Contact Information for Business Card

(Providing placeholder info for personal information, please design for longer character spaces, longer names and addresses etc..)
• Logo for Valdane
• Logo for Thornmere Regional Center
• Full name: Marcus Valdane
• Job title: CEO
• Email address: mvaldane@valdanecompanies.com
• Cell phone number: +1.555.314.2287
• Office number +1.555.628.4410
• Office address: Larkfield Court 5, 4817 Vista Orilla, Brightwater, OR.
• Website: www.valdanecompanies.com

Font styles to use
Serif
Sans Serif

Colors
ec1f27
ffffff
000000

Requirements
Must have
• • Logo for Valdane
• • Logo for Thornmere Regional Center
• - Use rounded corners
• (See .ai file included for logos)
Nice to have
• • Simple, elegant design
• • Aesthetically compatible with our website design (www.valdanecompanies.com)
• • Color palette including but not limited to white, black, and red (as per logos)
Should not have
• - Not too much red color
• - Do not stack both logos on top of each other

```html
<!DOCTYPE html>
<html lang="en">
<head>
<meta charset="utf-8">
<title>Valdane Companies – Business Card</title>
<link rel="stylesheet" href="https://fonts.googleapis.com/css2?family=Oswald:wght@500;600&family=Work+Sans:wght@400;600&display=swap">
<style>
  :root {
    --stage: #1b1b1b;
    --card-white: #ffffff;
    --card-black: #0c0c0c;
    --ink: #111111;
    --ink-soft: #2b2b2b;
    --rule: #3a3a3a;
    --silver: #c8c8c8;
    --mark: #2a2a2a;
  }
  * { box-sizing: border-box; margin: 0; padding: 0; }
  html, body { width: 1200px; height: 800px; overflow: hidden; }
  body {
    background: var(--stage);
    font-family: "Work Sans", Arial, sans-serif;
    position: relative;
  }
  .card {
    position: absolute;
    top: 252px;
    width: 520px;
    height: 297px;
    border-radius: 18px;
    overflow: hidden;
  }
  .card--front { left: 40px; background: var(--card-white); color: var(--ink); }
  .card--back { left: 640px; background: var(--card-black); border: 1px solid #262626; }

  .brand {
    position: absolute;
    display: flex;
    align-items: center;
    gap: 12px;
    font-family: "Work Sans", Arial, sans-serif;
    font-weight: 600;
    text-transform: uppercase;
    white-space: nowrap;
  }
  .brand__square { display: block; }
  .brand--capital { left: 190px; top: 62px; font-size: 21px; letter-spacing: 3px; color: var(--ink); }
  .brand--capital .brand__square { width: 22px; height: 22px; background: var(--mark); }

  .holder { position: absolute; left: 28px; top: 132px; width: 200px; text-align: right; }
  .holder__name {
    font-family: "Oswald", "Arial Narrow", sans-serif;
    font-weight: 600;
    font-size: 26px;
    letter-spacing: 0.5px;
    text-transform: uppercase;
    color: var(--ink-soft);
    line-height: 1.1;
    white-space: nowrap;
  }
  .holder__title { font-size: 13px; letter-spacing: 1px; color: var(--ink-soft); margin-top: 6px; }

  .divider { position: absolute; left: 248px; top: 132px; width: 1px; height: 82px; background: var(--rule); }

  .contact { position: absolute; left: 264px; top: 136px; list-style: none; }
  .contact__item {
    display: flex; align-items: center; gap: 8px;
    font-size: 12.5px; line-height: 19px; color: var(--ink-soft);
    white-space: nowrap;
  }
  .contact__icon { width: 10px; height: 10px; flex: none; }

  .address {
    position: absolute; left: 40px; bottom: 32px;
    display: flex; align-items: center; gap: 12px;
    font-size: 11px; letter-spacing: 1.2px; color: var(--ink-soft);
    white-space: nowrap;
  }
  .address__square { width: 12px; height: 12px; background: var(--mark); }

  .brand--regional {
    left: 50%; top: 50%; transform: translate(-50%, -50%);
    font-size: 19px; letter-spacing: 3px; color: var(--silver);
  }
  .brand--regional .brand__square { width: 26px; height: 26px; background: var(--silver); }
</style>
</head>
<body>
  <section class="card card--front" aria-label="Card front">
    <div class="brand brand--capital">
      <span class="brand__square"></span>
      <span class="brand__name">Valdane Capital</span>
    </div>

    <div class="holder">
      <p class="holder__name">Marcus Valdane</p>
      <p class="holder__title">CEO</p>
    </div>

    <span class="divider"></span>

    <ul class="contact">
      <li class="contact__item">
        <svg class="contact__icon" viewBox="0 0 10 10"><path d="M2 1 L3.6 1 L4.2 3 L3.2 3.8 Q4 5.8 6.2 6.8 L7 5.8 L9 6.4 L9 8 Q9 9 8 9 Q1 8.4 1 2 Q1 1 2 1 Z" fill="#2b2b2b"/></svg>
        <span>+1.555.314.2287</span>
      </li>
      <li class="contact__item">
        <svg class="contact__icon" viewBox="0 0 10 10"><rect x="2.5" y="0.5" width="5" height="9" rx="1" fill="none" stroke="#2b2b2b"/><circle cx="5" cy="8" r="0.6" fill="#2b2b2b"/></svg>
        <span>+1.555.628.4410</span>
      </li>
      <li class="contact__item">
        <svg class="contact__icon" viewBox="0 0 10 10"><rect x="0.5" y="2" width="9" height="6.5" fill="none" stroke="#2b2b2b"/><path d="M0.5 2 L5 5.6 L9.5 2" fill="none" stroke="#2b2b2b"/></svg>
        <span>mvaldane@valdanecompanies.com</span>
      </li>
      <li class="contact__item">
        <svg class="contact__icon" viewBox="0 0 10 10"><circle cx="5" cy="5" r="4.4" fill="none" stroke="#2b2b2b"/><ellipse cx="5" cy="5" rx="1.8" ry="4.4" fill="none" stroke="#2b2b2b"/><path d="M0.6 5 H9.4" stroke="#2b2b2b"/></svg>
        <span>www.valdanecompanies.com</span>
      </li>
    </ul>

    <div class="address">
      <span class="address__square"></span>
      <span>Larkfield Court 5, 4817 Vista Orilla, Brightwater, OR.</span>
    </div>
  </section>

  <section class="card card--back" aria-label="Card back">
    <div class="brand brand--regional">
      <span class="brand__square"></span>
      <span class="brand__name">Thornmere Regional Center</span>
    </div>
  </section>
</body>
</html>
```